Corporate-Design für Steuerberatungsgesellschaft
Zielgruppe
Wir sind eine Steuerberatungsgesellschaft mit 10 Mitarbeitern im Norden von Deutschland, kurz vor der Ostseeküste. Unser Unternehmen besteht seit 30 Jahren. Wir betreuen vor allem Mandanten in kleinen und mittleren Unternehmen: von der Arztpraxis bis zum Bauunternehmen. Demnächst werden wir neue Räume beziehen. Diese sollen großzügiger und moderner werden, teilweise mit Glaswänden.
Aufgabenstellung
Unser bisheriges Farbkonzept war von bordeaux und creme geprägt (www.kanzlei-mervato.de). Das muss aber nicht weiter bestehen. Das bisherige Logo finden wir inhaltlich recht treffend, aber es sollte moderner gestaltet werden. Der Schriftzug des Kanzleinamens soll an der Fassade in silbernen Buchstaben angebracht werden.

```html
<!DOCTYPE html>
<html lang="de">
<head>
<meta charset="utf-8">
<title>Mervato Steuerberatung – Corporate Design</title>
<link href="https://fonts.googleapis.com/css2?family=Noto+Serif:wght@400;700&display=swap" rel="stylesheet">
<style>
  :root{
    --red:#9b1b2a;
    --ink:#363636;
    --dark-card:#3a3a3c;
    --white:#ffffff;
    --stage-grey:#bdbdc1;
    --stage-sage:#e2e6e2;
    --paper:#f4f4f4;
  }
  *{margin:0;padding:0;box-sizing:border-box}
  html,body{width:1200px;height:2416px;overflow:hidden}
  body{font-family:"Noto Serif",Georgia,serif;color:var(--ink);background:var(--white);position:relative}
  .section{position:absolute;left:0;width:1200px}
  .brand-section{top:0;height:570px;background:var(--white)}
  .cards-section{top:570px;height:766px;background:var(--stage-grey)}
  .letter-section{top:1336px;height:1080px;background:var(--stage-sage)}

  .brand-name{position:absolute;display:flex;align-items:center;gap:18px;font-weight:700;color:var(--red);white-space:nowrap}
  .brand-name .mark{display:block;flex:none;background:var(--red)}
  .brand-section .brand-name{left:0;right:0;top:250px;justify-content:center;font-size:64px;letter-spacing:2px}
  .brand-section .mark{width:56px;height:56px}

  .card{position:absolute;width:460px;height:284px;overflow:hidden;box-shadow:0 6px 18px rgba(0,0,0,.18)}
  .card-back{left:100px;top:241px;background:var(--dark-card);color:var(--white)}
  .card-back .brand-name{left:44px;top:86px;font-size:26px;color:var(--white);gap:12px}
  .card-back .mark{width:20px;height:20px;background:var(--red)}
  .card-back .services{position:absolute;left:44px;top:198px;font-size:11px;line-height:16px;color:#e6e6e6}
  .card-back .band{position:absolute;left:0;right:0;bottom:34px;height:5px;background:var(--red)}

  .card-front{left:640px;top:241px;background:var(--white)}
  .card-front .person{position:absolute;left:26px;top:26px;font-size:10.5px;line-height:15px}
  .card-front .person .name{font-size:15px;font-weight:700;color:var(--red);line-height:21px;white-space:nowrap}
  .card-front .office{position:absolute;left:272px;top:26px;font-size:9.5px;line-height:14px;white-space:nowrap}
  .card-front .office b{color:var(--red)}
  .card-front .contacts{position:absolute;left:272px;top:116px;font-size:9.5px;line-height:16px;list-style:none;white-space:nowrap}
  .contacts li{display:flex;align-items:center;gap:7px}
  .contacts svg{width:10px;height:10px;flex:none}
  .card-front .band{position:absolute;right:0;bottom:40px;width:210px;height:4px;background:var(--red)}

  .sheet{position:absolute;left:312px;top:164px;width:576px;height:816px;background:var(--paper);box-shadow:0 14px 40px rgba(0,0,0,.16)}
  .sheet .brand-name{right:22px;top:30px;font-size:24px;gap:9px}
  .sheet .mark{width:18px;height:18px}
  .sender{position:absolute;left:62px;top:126px;font-size:7px;line-height:11px}
  .sender b{font-weight:700}
  .sender-rule{position:absolute;left:0;top:150px;width:190px;height:1.5px;background:var(--red)}
  .sheet .contacts{position:absolute;left:376px;top:114px;font-size:9px;line-height:14px;list-style:none}
  .sheet .contacts svg{width:9px;height:9px}
  .contact-rule{position:absolute;left:376px;right:0;top:184px;height:1.5px;background:var(--red)}
  .managers{position:absolute;left:376px;top:192px;font-size:9px;line-height:14px}
  .managers b{font-weight:700}
  .fold-mark{position:absolute;left:0;top:282px;width:4px;height:1px;background:var(--red)}
  .footer-band{position:absolute;left:0;bottom:0;width:405px;height:72px;background:var(--red);color:var(--white);padding:14px 0 0 56px;font-size:6.5px;line-height:17px;white-space:nowrap}
  .footer-band b{font-weight:700}
</style>
</head>
<body>

<section class="section brand-section">
  <div class="brand-name"><span class="mark"></span>Mervato Steuerberatung</div>
</section>

<section class="section cards-section">
  <article class="card card-back">
    <div class="brand-name"><span class="mark"></span>Mervato Steuerberatung</div>
    <p class="services">Steuerberatung / Finanz- und Lohnbuchhaltung<br>Betriebswirtschaftliche Beratung</p>
    <div class="band"></div>
  </article>

  <article class="card card-front">
    <div class="person">
      Diplom-Kaufmann
      <div class="name">Jonas Behrendt - Lohmann</div>
      Geschäftsführer / Steuerberater
    </div>
    <div class="office">
      <b>Mervato</b><br>
      <strong>Steuerberatungsgesellschaft mbH</strong><br>
      Dünenweg 4<br>
      D - 17391 Torvik
    </div>
    <ul class="contacts">
      <li><svg viewBox="0 0 10 10"><circle cx="5" cy="5" r="5" fill="#9b1b2a"/><path d="M3 2.6l1 1-.5.7a3 3 0 0 0 2.2 2.2l.7-.5 1 1-.7.9A4.5 4.5 0 0 1 2.1 3.3z" fill="#fff"/></svg>+49 (0) 30000 / 12 34 - 0</li>
      <li><svg viewBox="0 0 10 10"><circle cx="5" cy="5" r="5" fill="#9b1b2a"/><rect x="2.6" y="4" width="4.8" height="3" fill="#fff"/><rect x="3.4" y="2.6" width="3.2" height="1.6" fill="#fff"/></svg>+49 (0) 30000 / 12 34 - 49</li>
      <li><svg viewBox="0 0 10 10"><circle cx="5" cy="5" r="5" fill="#9b1b2a"/><rect x="2.5" y="3.2" width="5" height="3.6" fill="#fff"/><path d="M2.5 3.2L5 5.2l2.5-2" stroke="#9b1b2a" stroke-width=".6" fill="none"/></svg>kontakt@kanzlei-mervato.de</li>
      <li><svg viewBox="0 0 10 10"><circle cx="5" cy="5" r="5" fill="#9b1b2a"/><circle cx="5" cy="5" r="2.6" fill="none" stroke="#fff" stroke-width=".7"/><path d="M2.4 5h5.2M5 2.4v5.2" stroke="#fff" stroke-width=".5"/></svg>www.kanzlei-mervato.de</li>
    </ul>
    <div class="band"></div>
  </article>
</section>

<section class="section letter-section">
  <article class="sheet">
    <div class="brand-name"><span class="mark"></span>Mervato Steuerberatung</div>

    <p class="sender"><b>Mervato Steuerberatungsgesellschaft mbH</b><br>Dünenweg 4 • D - 17391 Torvik</p>
    <div class="sender-rule"></div>

    <ul class="contacts">
      <li><svg viewBox="0 0 10 10"><circle cx="5" cy="5" r="5" fill="#9b1b2a"/><path d="M3 2.6l1 1-.5.7a3 3 0 0 0 2.2 2.2l.7-.5 1 1-.7.9A4.5 4.5 0 0 1 2.1 3.3z" fill="#fff"/></svg>+49 (0) 30000 / 12 34-0</li>
      <li><svg viewBox="0 0 10 10"><circle cx="5" cy="5" r="5" fill="#9b1b2a"/><rect x="2.6" y="4" width="4.8" height="3" fill="#fff"/><rect x="3.4" y="2.6" width="3.2" height="1.6" fill="#fff"/></svg>+49 (0) 30000 / 12 34-49</li>
      <li><svg viewBox="0 0 10 10"><circle cx="5" cy="5" r="5" fill="#9b1b2a"/><rect x="2.5" y="3.2" width="5" height="3.6" fill="#fff"/><path d="M2.5 3.2L5 5.2l2.5-2" stroke="#9b1b2a" stroke-width=".6" fill="none"/></svg>kontakt@kanzlei-mervato.de</li>
      <li><svg viewBox="0 0 10 10"><circle cx="5" cy="5" r="5" fill="#9b1b2a"/><circle cx="5" cy="5" r="2.6" fill="none" stroke="#fff" stroke-width=".7"/><path d="M2.4 5h5.2M5 2.4v5.2" stroke="#fff" stroke-width=".5"/></svg>www.kanzlei-mervato.de</li>
    </ul>
    <div class="contact-rule"></div>

    <div class="managers">
      Geschäftsführer:<br>
      <b>Jonas Behrendt - Lohmann</b><br>
      Steuerberater / Dipl. Kaufmann<br>
      <b>Till Averbeck</b><br>
      Steuerberater
    </div>

    <div class="fold-mark"></div>

    <footer class="footer-band">
      <b>Mervato Steuerberatungsgesellschaft mbH</b> • Dünenweg 4 • D - 17391 Torvik<br>
      <b>USt-IdNr.</b> DE000000000 • AG Torvik • HRB 0000<br>
      Sparkasse Torvik • <b>IBAN</b> DE00 0000 0000 0000 0000 00 • <b>BIC</b> XXXXDEX1ABC
    </footer>
  </article>
</section>

</body>
</html>
```